Fenwick Grading LTD - website for irrigation & Landscape Lighting & Buried service wire

Looking for a website to help promote my business with Irrigation (installation, service, etc) and buried service wire/drainage solutions.

Commercial/Residential

Landscape lighting.

I’ll get photos in the trucks and trailers to upload as well maybe the machine as well.

Target Market(s)

Homeowners who want green grass and beautiful gardens. Beautiful landscape lighting

Industry/Entity Type

Irrigation systems and landscape lighting and buried service wire to homes and offering Drainage soltions.

Coding

Coded - Design and coding required

Number of Pages Required

4 page

Colors
F0912C
F2A743
F7CA91
FBE8D2
FDF5EE

Requirements
Must have
• was hoping to link up my email on fenwickgrading@mailbox-example.net with the website if possible.
Nice to have
• Page for Irrigation, page for landscape lighting, page buried service wire & drainage soltions.

```html
<!DOCTYPE html>
<html lang="en">
<head>
<meta charset="utf-8">
<title>Fenwick Grading LTD</title>
<link href="https://fonts.googleapis.com/css2?family=Michroma&family=Roboto:wght@400;500;700&display=swap" rel="stylesheet">
<style>
:root{
  --orange:#f0912c;
  --orange-2:#f2a743;
  --orange-3:#f7ca91;
  --cream:#fbe8d2;
  --gray:#7b7b7d;
  --gray-dark:#5f5f61;
  --ink:#1f2a3a;
  --text:#5b5b5b;
  --white:#fff;
}
*{box-sizing:border-box;margin:0;padding:0}
html,body{width:1200px;height:2905px;overflow:hidden}
body{position:relative;font-family:'Roboto',sans-serif;color:var(--text);background:var(--white)}
.abs{position:absolute}
.bg{position:absolute;left:0;top:0;z-index:0}
.display{font-family:'Michroma',sans-serif;font-weight:400}

/* header */
.topline{left:0;top:0;width:1200px;height:3px;background:var(--orange);z-index:2}
.brand{left:143px;top:34px;z-index:2;display:flex;align-items:center;gap:10px}
.brand-dot{width:16px;height:16px;border-radius:50%;background:var(--orange)}
.brand-name{font-family:'Michroma',sans-serif;font-size:21px;line-height:1.15;color:var(--orange);width:170px}
.contact-item{top:20px;z-index:2;display:flex;align-items:center;gap:12px}
.contact-icon{width:38px;height:38px;border-radius:50%;background:var(--orange);display:flex;align-items:center;justify-content:center}
.contact-label{font-size:12px;color:#666}
.contact-value{font-size:19px;color:#222}
.nav{left:423px;top:77px;width:777px;height:39px;z-index:2}
.nav ul{list-style:none;display:flex;position:absolute;left:30px;top:0;height:39px;align-items:center}
.nav li{color:#fff;font-size:15px;font-weight:500;margin-right:50px}
.nav .cta{position:absolute;left:515px;top:0;width:119px;height:39px;background:var(--orange);color:#fff;font-weight:500;font-size:15px;display:flex;align-items:center;justify-content:center}

/* hero */
.hero-title{left:143px;top:310px;font-size:40px;color:#fff;z-index:2;letter-spacing:1px}
.hero-text{left:143px;top:373px;width:440px;font-size:16px;line-height:24px;color:#fff;font-weight:500;z-index:2}
.btn{display:inline-flex;align-items:center;gap:8px;background:var(--orange);color:#fff;font-weight:700;border-radius:30px;z-index:2}
.hero-btn{left:143px;top:455px;height:43px;padding:0 28px;font-size:16px}
.scroll-ring{width:80px;height:80px;border-radius:50%;border:2px solid #fff;display:flex;align-items:center;justify-content:center;z-index:3}
.scroll-ring span{width:64px;height:64px;border-radius:50%;background:#fff;display:flex;align-items:center;justify-content:center;box-shadow:0 3px 10px rgba(0,0,0,.15)}

/* about */
.about-visual{left:68px;top:788px;width:496px;height:306px;z-index:1;clip-path:polygon(0 14%,100% 14%,46% 100%);background:linear-gradient(135deg,#6f8a3b,#c47c2b 45%,#4f7a57)}
.about-kicker{left:628px;top:784px;font-size:18px;font-weight:500;color:var(--orange);z-index:2}
.about-title{left:628px;top:812px;font-size:29px;color:var(--gray);z-index:2}
.about-body{left:628px;top:860px;width:428px;z-index:2;font-size:14px;line-height:23.5px;text-align:justify}
.about-body p{margin-bottom:8px}
.about-btn{left:628px;top:1055px;height:40px;padding:0 36px;font-size:15px}

/* services */
.services-title{left:0;top:1322px;width:1200px;text-align:center;font-size:32px;color:#fff;z-index:2}
.services-sub{left:0;top:1382px;width:1200px;text-align:center;font-size:18px;font-weight:500;color:#fff;z-index:2}
.service{top:1450px;width:300px;text-align:center;z-index:2;color:#fff;padding-top:20px}
.service.featured{background:#fff;color:var(--text);border-radius:26px;width:314px;height:343px;box-shadow:0 6px 0 var(--gray)}
.service-icon{width:108px;height:108px;border-radius:50%;background:#fff;margin:0 auto;display:flex;align-items:center;justify-content:center}
.featured .service-icon{background:var(--gray)}
.service h3{font-size:18px;font-weight:500;margin:27px 0 14px;letter-spacing:.3px}
.featured h3{color:#222}
.service p{font-size:14px;line-height:22.5px;padding:0 28px}
.service .more{display:inline-flex;align-items:center;gap:6px;font-size:13px;font-weight:700;margin-top:18px}
.featured .more{color:var(--orange)}

/* blog */
.blog-title{left:0;top:1988px;width:1200px;text-align:center;font-size:36px;color:var(--gray);z-index:2}
.blog-title em{font-style:normal;color:var(--orange)}
.post{top:2059px;width:290px;height:306px;z-index:2}
.post-photo{position:absolute;left:0;top:0;width:290px;height:200px}
.post-date{position:absolute;right:17px;top:16px;width:40px;height:46px;background:var(--orange);color:#fff;border-radius:6px;font-size:13px;font-weight:500;text-align:center;line-height:17px;padding-top:6px}
.post-card{position:absolute;left:18px;top:180px;width:272px;height:126px;background:#fff;box-shadow:0 4px 14px rgba(0,0,0,.12);padding:18px 22px}
.post-cat{font-size:12px;color:#888;display:flex;gap:8px;align-items:center}
.post-card h4{font-size:16px;line-height:22px;color:var(--ink);font-weight:500;margin:8px 0 10px}
.post-meta{font-size:12px;color:#888;display:flex;gap:18px}
.post-meta span{display:flex;gap:6px;align-items:center}
.post-meta b{color:var(--orange-2);font-weight:400}

/* footer */
.footer-brand{left:143px;top:2640px;z-index:2;display:flex;align-items:center;gap:10px}
.footer-brand .brand-name{color:#fff;font-size:24px;width:210px}
.footer-col{top:2584px;z-index:2;color:#fff}
.footer-col h5{font-size:17px;font-weight:700;letter-spacing:.3px;padding-bottom:10px;position:relative}
.footer-col h5::after{content:"";position:absolute;left:0;bottom:0;width:58px;height:2px;background:var(--orange)}
.links{list-style:none;margin-top:16px;padding-left:6px}
.links li{font-size:11px;line-height:24px}
.info{list-style:none;margin-top:18px}
.info li{display:flex;gap:10px;align-items:flex-start;font-size:11px;line-height:18px;margin-bottom:14px}
.info .ic{flex:none;width:22px;height:22px;border-radius:50%;background:var(--orange);display:flex;align-items:center;justify-content:center}
.sub-text{font-size:11px;line-height:19px;margin-top:16px;width:240px}
.sub-form{margin-top:14px;display:flex;width:234px;height:34px}
.sub-form span{flex:1;background:#fff;border-radius:17px 0 0 17px;font-size:9px;color:#666;display:flex;align-items:center;padding-left:12px;gap:5px}
.sub-form b{width:44px;background:var(--orange);border-radius:0 17px 17px 0;display:flex;align-items:center;justify-content:center}
.social{margin-top:18px;width:28px;height:28px;border-radius:50%;background:#fff}
.bottombar{left:0;top:2852px;width:1200px;height:53px;background:var(--gray-dark);z-index:2;color:#fff;font-size:12px}
.bottombar .left{position:absolute;left:143px;top:20px}
.bottombar .left u{color:var(--orange)}
.bottombar .right{position:absolute;right:143px;top:20px}
</style>
</head>
<body>

<svg class="bg" width="1200" height="2905" viewBox="0 0 1200 2905" aria-hidden="true">
  <defs>
    <linearGradient id="heroGrad" x1="0" y1="0" x2="1" y2="1">
      <stop offset="0" stop-color="#2f3b23"/>
      <stop offset=".45" stop-color="#4f6a2a"/>
      <stop offset=".75" stop-color="#6b8a30"/>
      <stop offset="1" stop-color="#3a3024"/>
    </linearGradient>
    <linearGradient id="orangeGrad" x1="0" y1="0" x2="1" y2="1">
      <stop offset="0" stop-color="#ee8f2e"/>
      <stop offset="1" stop-color="#f0952f"/>
    </linearGradient>
  </defs>
  <rect x="0" y="116" width="1200" height="619" fill="url(#heroGrad)" role="img" aria-label="Evening garden photo with landscape path lights and lawn"/>
  <polygon points="600,735 1200,625 1200,802" fill="var(--gray)"/>
  <polygon points="0,1094 555,1218 0,1270" fill="var(--gray)"/>
  <polygon points="0,1270 1200,1162 1200,1870 0,1952" fill="url(#orangeGrad)"/>
  <polygon points="0,2436 1200,2480 1200,2905 0,2905" fill="var(--gray)"/>
  <polygon points="630,2525 1200,2374 1200,2512" fill="var(--orange)"/>
</svg>

<!-- header -->
<div class="abs topline"></div>
<div class="abs brand"><span class="brand-dot"></span><span class="brand-name">FENWICK GRADING LTD</span></div>
<div class="abs contact-item" style="left:534px">
  <span class="contact-icon"><svg width="18" height="14" viewBox="0 0 18 14"><rect x="1" y="1" width="16" height="12" rx="1" fill="none" stroke="#fff" stroke-width="1.8"/><path d="M1 2l8 6 8-6" fill="none" stroke="#fff" stroke-width="1.8"/></svg></span>
  <div><div class="contact-label">Email Us On</div><div class="contact-value" style="font-size:16px">fenwickgrading@mailbox-example.net</div></div>
</div>
<div class="abs contact-item" style="left:862px">
  <span class="contact-icon"><svg width="18" height="18" viewBox="0 0 24 24"><path d="M6.6 10.8a15 15 0 006.6 6.6l2.2-2.2a1 1 0 011-.25 11.4 11.4 0 003.6.57 1 1 0 011 1V20a1 1 0 01-1 1A17 17 0 013 4a1 1 0 011-1h3.5a1 1 0 011 1c0 1.25.2 2.45.57 3.57a1 1 0 01-.25 1z" fill="#fff"/></svg></span>
  <div><div class="contact-label">Call Us Today</div><div class="contact-value">+1-555-014-2290</div></div>
</div>
<nav class="abs nav">
  <svg class="bg" width="777" height="39" aria-hidden="true"><polygon points="0,39 30,0 777,0 777,39" fill="var(--gray)"/></svg>
  <ul><li>Home</li><li>About Us</li><li>Services</li><li>Projects</li><li>Blog</li></ul>
  <span class="cta">Contact</span>
</nav>

<!-- hero -->
<h1 class="abs hero-title display">FENWICK GRADING</h1>
<p class="abs hero-text">Lorem ipsum dolor sit amet, consectetur adipiscing elit, sed do eiusmod tempor incididunt ut labore et dolore.</p>
<span class="abs btn hero-btn">GET STARTED <svg width="15" height="15" viewBox="0 0 16 16"><circle cx="8" cy="8" r="8" fill="#fff"/><path d="M6.5 4.5L10 8l-3.5 3.5" fill="none" stroke="var(--orange)" stroke-width="2"/></svg></span>
<div class="abs scroll-ring" style="left:560px;top:638px"><span><svg width="28" height="24" viewBox="0 0 28 24"><path d="M4 4l10 9 10-9M4 12l10 9 10-9" fill="none" stroke="var(--gray)" stroke-width="2.4"/></svg></span></div>

<!-- about -->
<div class="abs about-visual" role="img" aria-label="Collage of irrigation and landscaping work photos in an angular frame"></div>
<div class="abs about-kicker">Welcome To</div>
<h2 class="abs about-title display">FENWICK GRADING</h2>
<div class="abs about-body">
  <p>Lorem ipsum dolor sit amet, consectetur adipiscing elit, sed do eiusmod tempor incididunt ut labore et dolore magna aliqua. Ut enim ad minim veniam, quis nostrud exercitation ullamco laboris nisi ut aliquip ex ea commodo consequat.</p>
  <p>Duis aute irure dolor in reprehenderit in voluptate velit esse cillum dolore eu fugiat nulla pariatur. Excepteur sint occaecat cupidatat non proident, sunt in culpa qui officia deserunt mollit anim .</p>
</div>
<span class="abs btn about-btn">READ MORE <svg width="14" height="14" viewBox="0 0 16 16"><circle cx="8" cy="8" r="8" fill="#fff"/><path d="M6.5 4.5L10 8l-3.5 3.5" fill="none" stroke="var(--orange)" stroke-width="2"/></svg></span>

<!-- services -->
<h2 class="abs services-title display">OUR SERVICES</h2>
<p class="abs services-sub">Homeowners who want green grass and beautiful gardens. Beautiful landscape lighting</p>

<div class="abs service" style="left:126px">
  <div class="service-icon"><svg width="54" height="54" viewBox="0 0 54 54" fill="none" stroke="var(--gray)" stroke-width="2"><rect x="6" y="6" width="42" height="6"/><path d="M14 12v6M40 12v6M12 22l-3 8M16 22l3 8M38 22l-3 8M42 22l3 8"/><path d="M8 48c0-8 4-12 10-12-1 6-4 10-10 12zM22 48c0-8-3-12-8-12M34 48c0-8 4-12 10-12-1 6-4 10-10 12zM48 48c0-8-3-12-8-12"/></svg></div>
  <h3>IRRIGATION INSTALLS</h3>
  <p>Lorem ipsum dolor sit amet, consectetur adipiscing elit, sed do eiusmod tempor incididunt ut labore et dolore.</p>
  <span class="more">READ MORE <svg width="20" height="12" viewBox="0 0 20 12" fill="none" stroke="#fff" stroke-width="2"><path d="M1 6h17M13 1l5 5-5 5"/></svg></span>
</div>
<div class="abs service featured" style="left:444px">
  <div class="service-icon"><svg width="58" height="58" viewBox="0 0 58 58" fill="none" stroke="#fff" stroke-width="2"><path d="M4 8h50M14 8v14M29 8v10M44 8v16"/><path d="M10 22h8l4 18H6zM25 18h8l5 16H20zM40 24h8v8l4 14H36l4-14z"/><path d="M4 52h50"/></svg></div>
  <h3>LANDSCAPE LIGHTING</h3>
  <p>Lorem ipsum dolor sit amet, consectetur adipiscing elit, sed do eiusmod tempor incididunt ut labore et dolore magna aliqua.</p>
  <span class="more">READ MORE <svg width="20" height="12" viewBox="0 0 20 12" fill="none" stroke="var(--orange)" stroke-width="2"><path d="M1 6h17M13 1l5 5-5 5"/></svg></span>
</div>
<div class="abs service" style="left:774px">
  <div class="service-icon"><svg width="58" height="58" viewBox="0 0 58 58" fill="none" stroke="var(--gray)" stroke-width="2"><circle cx="29" cy="29" r="16"/><path d="M29 4v7M29 47v7M4 29h7M47 29h7M11 11l5 5M42 42l5 5M11 47l5-5M42 16l5-5"/><path d="M21 37l16-16M24 40l16-16"/><circle cx="29" cy="29" r="25" stroke-dasharray="4 4"/></svg></div>
  <h3>FIBER OPTIC INSTALLATION</h3>
  <p>Lorem ipsum dolor sit amet, consectetur adipiscing elit, sed do eiusmod tempor incididunt ut labore et dolore.</p>
  <span class="more">READ MORE <svg width="20" height="12" viewBox="0 0 20 12" fill="none" stroke="#fff" stroke-width="2"><path d="M1 6h17M13 1l5 5-5 5"/></svg></span>
</div>

<!-- blog -->
<h2 class="abs blog-title display">LATEST <em>BLOG</em></h2>

<article class="abs post" style="left:143px">
  <div class="post-photo" role="img" aria-label="Drip irrigation hose being laid in a garden bed" style="background:linear-gradient(135deg,#5d7d4a,#7f8e95 50%,#b05a3e)"></div>
  <div class="post-date">Jul<br>12</div>
  <div class="post-card">
    <div class="post-cat"><svg width="10" height="11"><rect width="10" height="11" rx="1" fill="var(--orange-2)"/></svg>Lorem ipsum dolor</div>
    <h4>Lorem ipsum dolor sit amet sed conseum dolor sictea.</h4>
    <div class="post-meta"><span><svg width="10" height="11"><circle cx="5" cy="3" r="3" fill="var(--orange-2)"/><rect x="0" y="6" width="10" height="5" rx="2" fill="var(--orange-2)"/></svg>John Doe</span><span><svg width="12" height="10"><ellipse cx="6" cy="5" rx="6" ry="4.5" fill="var(--orange-2)"/></svg><b>0</b> Comments</span></div>
  </div>
</article>
<article class="abs post" style="left:455px">
  <div class="post-photo" role="img" aria-label="Technician operating a drone over green farm fields" style="background:linear-gradient(180deg,#d9dfd6,#8da06a 55%,#4f6b35)"></div>
  <div class="post-date">Aug<br>17</div>
  <div class="post-card">
    <div class="post-cat"><svg width="10" height="11"><rect width="10" height="11" rx="1" fill="var(--orange-2)"/></svg>Lorem ipsum dolor</div>
    <h4>Lorem ipsum dolor sit amet sed conseum dolor sictea.</h4>
    <div class="post-meta"><span><svg width="10" height="11"><circle cx="5" cy="3" r="3" fill="var(--orange-2)"/><rect x="0" y="6" width="10" height="5" rx="2" fill="var(--orange-2)"/></svg>John Doe</span><span><svg width="12" height="10"><ellipse cx="6" cy="5" rx="6" ry="4.5" fill="var(--orange-2)"/></svg><b>0</b> Comments</span></div>
  </div>
</article>
<article class="abs post" style="left:766px">
  <div class="post-photo" role="img" aria-label="Gloved hands testing a water sample over a bucket" style="background:linear-gradient(135deg,#2c3446,#8fb0c9 50%,#6d7a4a)"></div>
  <div class="post-date">Dec<br>24</div>
  <div class="post-card">
    <div class="post-cat"><svg width="10" height="11"><rect width="10" height="11" rx="1" fill="var(--orange-2)"/></svg>Lorem ipsum dolor</div>
    <h4>Lorem ipsum dolor sit amet sed conseum dolor sictea.</h4>
    <div class="post-meta"><span><svg width="10" height="11"><circle cx="5" cy="3" r="3" fill="var(--orange-2)"/><rect x="0" y="6" width="10" height="5" rx="2" fill="var(--orange-2)"/></svg>John Doe</span><span><svg width="12" height="10"><ellipse cx="6" cy="5" rx="6" ry="4.5" fill="var(--orange-2)"/></svg><b>0</b> Comments</span></div>
  </div>
</article>

<!-- footer -->
<div class="abs scroll-ring" style="left:560px;top:2452px"><span><svg width="28" height="24" viewBox="0 0 28 24"><path d="M4 20l10-9 10 9M4 12l10-9 10 9" fill="none" stroke="var(--gray)" stroke-width="2.4"/></svg></span></div>

<div class="abs footer-brand"><span class="brand-dot"></span><span class="brand-name">FENWICK GRADING LTD</span></div>

<div class="abs footer-col" style="left:384px">
  <h5>QUICK LINKS</h5>
  <ul class="links"><li>Home</li><li>About Us</li><li>Services</li><li>Projects</li><li>Blog</li><li>Contact Us</li></ul>
</div>
<div class="abs footer-col" style="left:549px">
  <h5>CONTACT US</h5>
  <ul class="info">
    <li><span class="ic"><svg width="11" height="11" viewBox="0 0 24 24"><path d="M6.6 10.8a15 15 0 006.6 6.6l2.2-2.2a1 1 0 011-.25 11.4 11.4 0 003.6.57 1 1 0 011 1V20a1 1 0 01-1 1A17 17 0 013 4a1 1 0 011-1h3.5a1 1 0 011 1c0 1.25.2 2.45.57 3.57a1 1 0 01-.25 1z" fill="#fff"/></svg></span><span style="padding-top:2px">+1-555-014-2290</span></li>
    <li><span class="ic"><svg width="11" height="9" viewBox="0 0 18 14"><rect x="1" y="1" width="16" height="12" fill="#fff"/><path d="M1 2l8 6 8-6" fill="none" stroke="var(--orange)" stroke-width="1.8"/></svg></span><span style="padding-top:2px">fenwickgrading@mailbox-example.net</span></li>
    <li><span class="ic"><svg width="10" height="12" viewBox="0 0 10 12"><path d="M5 12S0 7 0 4.5a5 5 0 0110 0C10 7 5 12 5 12z" fill="#fff"/><circle cx="5" cy="4.5" r="1.8" fill="var(--orange)"/></svg></span><span>Lorem ipsum dolor sit amet,<br>consectetur adipiscing 58571</span></li>
    <li><span class="ic"><svg width="11" height="11" viewBox="0 0 12 12"><rect x="1" y="3" width="10" height="8" rx="1" fill="#fff"/><rect x="3" y="1" width="6" height="3" fill="#fff"/></svg></span><span style="padding-top:2px">+1 555 019 3377</span></li>
  </ul>
</div>
<div class="abs footer-col" style="left:821px">
  <h5>SUBSCRIBE TO OUR MAIL</h5>
  <p class="sub-text">Irrigation systems and landscape lighting and fiber optic installation to homes.</p>
  <div class="sub-form"><span><svg width="10" height="8" viewBox="0 0 18 14"><rect x="1" y="1" width="16" height="12" fill="none" stroke="#666" stroke-width="2"/><path d="M1 2l8 6 8-6" fill="none" stroke="#666" stroke-width="2"/></svg>Email Address</span><b><svg width="16" height="14" viewBox="0 0 16 14"><path d="M0 6L16 0 12 14 7 9z" fill="#fff"/></svg></b></div>
  <div class="social"></div>
</div>

<div class="abs bottombar">
  <span class="left">Copyright© 2024 <u>Fenwick Grading</u> &nbsp;|&nbsp; All Rights Reserved</span>
  <span class="right">Terms and Conditions &nbsp;&nbsp;|&nbsp;&nbsp; Privacy Policy</span>
</div>

</body>
</html>
```